Business card for marketing analytics company

Need a business card for new company. I have a logo already that I want to be built into the card and should use those colours

Company is called steered by tallies
Design must bring steered by tallies to life not be a card that could be for anyone with a logo put on it.

Like the front to be fairly clean and uncluttered bringing the logo out with a suitable design on the back of the card.

The logo represents a compass and business growth so those themes along with numbers, analytics , data are appropriate.
I'm often working with creative industries so also needs to reflect the creative side of analytics rather than be very corporate looking.

Target Market(s)

Ad agency, media agency, consumer goods clients

Industry/Entity Type

Market Research

Contact Information for Business Card

Needs to include name, title, email and phone number

Colors
f78f20
f68d4d
ec1f27

Requirements
Must have
• Must bring steered by tallies to life not be a card that could be for anyone with a logo put on it.
• Logo, Correct colours
• Like a design on the back that relates to company name
• Designs for both sides
Should not have
• Please do not just submit logo and a coloured card.
• It needs to have a design element to it
• No black background
• No clear cards - needs front & back

```html
<!DOCTYPE html>
<html lang="en">
<head>
<meta charset="utf-8">
<title>Steered by Tallies – Business Card</title>
<link rel="stylesheet" href="https://fonts.googleapis.com/css2?family=Montserrat:wght@400;500;600;700&display=swap">
<style>
  :root {
    --brand-red: #c11f26;
    --brand-red-deep: #b51c23;
    --brand-red-soft: #d0343a;
    --brand-orange: #f78f20;
    --brand-coral: #f68d4d;
    --card-white: #ffffff;
    --canvas-bg: #e6e6e6;
    --ink-light: #ffffff;
  }
  * { box-sizing: border-box; margin: 0; padding: 0; }
  html, body {
    width: 1200px;
    height: 1000px;
    overflow: hidden;
    background: var(--canvas-bg);
    font-family: "Montserrat", Arial, sans-serif;
  }
  .stage {
    position: relative;
    width: 1200px;
    height: 1000px;
  }
  .card {
    position: absolute;
    top: 350px;
    width: 520px;
    height: 300px;
    overflow: hidden;
    box-shadow: 0 4px 14px rgba(0, 0, 0, 0.18);
  }
  .card--front { left: 60px; }
  .card--back  { left: 620px; background: var(--brand-red); }

  .card__art {
    position: absolute;
    inset: 0;
    width: 100%;
    height: 100%;
  }

  .contact {
    position: absolute;
    left: 26px;
    top: 76px;
    color: var(--ink-light);
  }
  .contact__name {
    font-size: 17px;
    font-weight: 700;
    letter-spacing: 0.3px;
    line-height: 1.1;
  }
  .contact__title {
    font-size: 10px;
    font-weight: 600;
    letter-spacing: 0.5px;
    margin-top: 3px;
  }
  .contact__list {
    list-style: none;
    margin-top: 18px;
  }
  .contact__item {
    display: flex;
    align-items: center;
    gap: 8px;
    font-size: 11px;
    font-weight: 500;
    height: 18px;
  }
  .contact__icon {
    width: 13px;
    height: 13px;
    flex: none;
  }
  .contact__address {
    margin-top: 14px;
    font-size: 11px;
    font-weight: 500;
    line-height: 1.4;
  }

  .brand {
    position: absolute;
    display: flex;
    align-items: center;
    gap: 10px;
  }
  .brand__dot {
    width: 44px;
    height: 44px;
    border-radius: 50%;
    flex: none;
  }
  .brand__name {
    font-size: 21px;
    font-weight: 600;
    line-height: 1.05;
    white-space: nowrap;
  }
  .brand--front {
    left: 286px;
    top: 126px;
  }
  .brand--front .brand__dot { border: 3px solid var(--brand-coral); }
  .brand--front .brand__name { color: var(--brand-coral); }

  .brand--back {
    left: 50%;
    top: 50%;
    transform: translate(-50%, -50%);
    gap: 14px;
  }
  .brand--back .brand__dot {
    width: 64px;
    height: 64px;
    border: 3px solid var(--ink-light);
  }
  .brand--back .brand__name {
    color: var(--ink-light);
    font-size: 27px;
  }
</style>
</head>
<body>
<main class="stage">

  <section class="card card--front" aria-label="Business card front">
    <svg class="card__art" viewBox="0 0 520 300" aria-hidden="true">
      <rect width="520" height="300" fill="var(--brand-red)"/>
      <path d="M322 0 Q170 150 328 300 L520 300 L520 0 Z" fill="var(--brand-orange)"/>
      <path d="M340 0 Q190 150 342 300 L520 300 L520 0 Z" fill="var(--brand-red-deep)"/>
      <path d="M352 0 Q208 150 352 300 L520 300 L520 0 Z" fill="var(--card-white)"/>
    </svg>

    <div class="contact">
      <p class="contact__name">DANA WHITFIELD</p>
      <p class="contact__title">FOUNDER</p>
      <ul class="contact__list">
        <li class="contact__item">
          <svg class="contact__icon" viewBox="0 0 16 16" aria-hidden="true">
            <circle cx="8" cy="8" r="8" fill="#fff"/>
            <path d="M5.2 4.2l1.4-.4 1 2.1-.9.8c.5 1 1.3 1.8 2.3 2.3l.8-.9 2.1 1-.4 1.4c-3.3.1-6.4-3-6.3-6.3z" fill="var(--brand-red)"/>
          </svg>
          000 000 0000
        </li>
        <li class="contact__item">
          <svg class="contact__icon" viewBox="0 0 16 16" aria-hidden="true">
            <circle cx="8" cy="8" r="8" fill="#fff"/>
            <rect x="4" y="5" width="8" height="6" rx="0.8" fill="var(--brand-red)"/>
            <path d="M4.4 5.5L8 8.3l3.6-2.8" stroke="#fff" stroke-width="0.9" fill="none"/>
          </svg>
          info@danawhitfield.com
        </li>
        <li class="contact__item">
          <svg class="contact__icon" viewBox="0 0 16 16" aria-hidden="true">
            <circle cx="8" cy="8" r="8" fill="#fff"/>
            <circle cx="8" cy="8" r="4" fill="none" stroke="var(--brand-red)" stroke-width="1"/>
            <path d="M4 8h8M8 4c-1.6 2.4-1.6 5.6 0 8M8 4c1.6 2.4 1.6 5.6 0 8" stroke="var(--brand-red)" stroke-width="0.9" fill="none"/>
          </svg>
          yourwebsitename.com
        </li>
      </ul>
      <p class="contact__address">418 Willow Creek Road,<br>Suite 210, Dayton, OH 45402</p>
    </div>

    <div class="brand brand--front">
      <span class="brand__dot"></span>
      <span class="brand__name">Steered by<br>Tallies</span>
    </div>
  </section>

  <section class="card card--back" aria-label="Business card back">
    <svg class="card__art" viewBox="0 0 520 300" aria-hidden="true">
      <rect width="520" height="300" fill="var(--brand-red)"/>
      <!-- rising growth line and tally bars -->
      <g class="growth-bars" fill="var(--brand-red-soft)">
        <rect x="24" y="262" width="14" height="38"/>
        <rect x="46" y="250" width="14" height="50"/>
        <rect x="68" y="236" width="14" height="64"/>
        <rect x="90" y="244" width="14" height="56"/>
        <rect x="112" y="222" width="14" height="78"/>
        <rect x="134" y="206" width="14" height="94"/>
      </g>
      <polyline class="growth-line" points="20,270 52,252 76,240 98,248 120,226 142,208 170,186"
        fill="none" stroke="var(--brand-orange)" stroke-width="2.5" stroke-linecap="round" stroke-linejoin="round"/>
      <circle cx="170" cy="186" r="4" fill="var(--brand-orange)"/>
      <!-- sweeping arcs echoing the front -->
      <path d="M430 0 Q560 150 470 300" fill="none" stroke="var(--brand-orange)" stroke-width="6"/>
      <path d="M452 0 Q580 150 492 300" fill="none" stroke="var(--brand-red-soft)" stroke-width="10"/>
    </svg>
    <div class="brand brand--back">
      <span class="brand__dot"></span>
      <span class="brand__name">Steered by<br>Tallies</span>
    </div>
  </section>

</main>
</body>
</html>
```